Redo a PPT pres. - Real Estate in Brazil - Socially equitable investments in Social Housing

We need to redo the presentation attached. It is an institutional presentation to attract local and foreign investors to invest in Brazilian Social Housing Projects structured by our company "TLR".
A middle class of 100 million, a housing deficit of 9M, a strong political will & positive income generation trends constitute grounds for a significant demand in social housing.
This make a perfect scheme for investors to invest in Brazilian Social Housing.
"TLR", is a consulting "boutique" focused in Brazilian real estate, specialized in structuring, analyzing and originating Brazilian social housing projects.
TLR is part of the group TLB. TLB is structured to create value through each step of the residential real estate business - structuring, financing, sales, marketing and technology.
We would like to see designs that use mainly the color blue. The final design should communicate financial safety and professionalism. In order to reach our needs, the designer will need to have basic understanding of finance and investment in order to highlight the most important information.
The idea is to receive back the PPT with each page redesigned and an homogeneous identity.
To all designers,
Target Market(s)
Institutional Investors and wealthy individuals
Industry/Entity Type
Residential
Look and feel

```html
<!DOCTYPE html>
<html lang="en">
<head>
<meta charset="utf-8">
<title>TLR – Brazilian Social Housing</title>
<link rel="stylesheet" href="https://fonts.googleapis.com/css2?family=PT+Sans:ital,wght@0,400;0,700;1,400&display=swap">
<style>
:root{
  --page:#ffffff;
  --navy:#1d4f8c;
  --blue:#2a6db5;
  --sky:#3d8fd6;
  --pale:#9ec6ea;
  --mist:#dfe9f4;
  --ink:#555b63;
  --rule:#c9d2dc;
}
*{box-sizing:border-box;margin:0;padding:0}
html,body{width:1200px;height:329px;overflow:hidden;background:var(--page)}
body{position:relative;font-family:"PT Sans",Arial,sans-serif;color:var(--ink)}
.slide{position:absolute;top:42px;width:342px;height:250px;background:#fff;box-shadow:0 1px 5px rgba(0,0,0,.35);overflow:hidden}
.s1{left:22px}.s2{left:428px}.s3{left:823px}
.header{position:absolute;left:0;top:0;width:100%;height:44px;background:var(--blue)}
.title{position:absolute;left:12px;top:6px;width:210px;color:#fff;font-size:13px;line-height:15px;font-weight:400}
.skyline{position:absolute;right:0;top:4px;width:120px;height:40px;background:linear-gradient(180deg,rgba(255,255,255,.15),rgba(255,255,255,.85))}
.footer-brand{position:absolute;left:10px;bottom:7px;font-size:8px;color:var(--navy);font-weight:700;display:flex;align-items:center;gap:2px}
.footer-brand i{width:4px;height:4px;background:var(--navy);display:block}
.page-no{position:absolute;right:10px;bottom:8px;font-size:5px}
.footer-bar{position:absolute;left:0;bottom:0;width:100%;height:3px;background:var(--blue)}
.lights{position:absolute;left:35px;top:76px;width:200px;height:120px;background:linear-gradient(90deg,var(--navy),var(--sky),var(--pale))}
.green-light{position:absolute;left:245px;top:100px;font-size:23px;font-weight:700;line-height:26px;color:var(--sky)}
.icon-light{position:absolute;right:10px;top:48px;width:14px;height:22px;background:var(--sky)}
.col-left{position:absolute;left:13px;top:52px;width:154px;font-size:5.9px;line-height:7px}
h3{font-size:8px;color:var(--navy);line-height:10px}
.col-left ul{list-style:none;margin-top:2px}
.col-left li.main{color:var(--blue);margin-top:2px}
.col-left li.main::before{content:"• "}
.col-left li.sub{padding-left:14px;text-indent:-5px}
.col-left li.sub::before{content:"– "}
.divider{position:absolute;left:170px;top:52px;width:1px;height:185px;background:var(--rule)}
.arrow{position:absolute;left:170px;top:68px;width:0;height:0;border-top:9px solid transparent;border-bottom:9px solid transparent;border-left:8px solid var(--sky)}
.lead{position:absolute;left:180px;top:50px;width:140px;font-size:6px;line-height:7px;color:var(--sky)}
.box{position:absolute;left:184px;top:84px;width:140px;height:137px;border:1px solid var(--pale);background:var(--mist);padding:5px 6px}
.box h4{font-size:9px;line-height:10px;color:var(--blue);font-weight:700}
.box ul{list-style:none;font-size:5.7px;line-height:6.7px;margin-top:3px}
.box li{padding-left:5px;text-indent:-4px;margin-bottom:1px}
.box li::before{content:"• "}
.box li.key{color:var(--blue);font-weight:700}
.sub-lead{position:absolute;left:12px;top:50px;font-size:6px;color:var(--sky)}
.chart{position:absolute}
.chart text{font-family:"PT Sans",Arial,sans-serif;fill:var(--ink)}
.buyers{position:absolute;left:12px;top:148px;width:150px;font-size:5.2px;line-height:6px}
.buyers h3{font-size:6.5px;line-height:8px;color:var(--blue)}
.buyers li{list-style:none;padding-left:4px;text-indent:-4px}
.buyers li::before{content:"• "}
.buyers .hi{color:var(--blue)}
.buyers .out{color:var(--blue);margin-bottom:2px}
.buyers .out::before{content:"→ "}
</style>
</head>
<body>

<section class="slide s1">
  <div class="header"><h2 class="title">Macro-environment &amp; mortgage market</h2><div class="skyline" role="img" aria-label="City skyline silhouette"></div></div>
  <div class="lights" role="img" aria-label="Three traffic lights in shades of blue, the middle one marked 1"></div>
  <div class="green-light">GREEN<br>LIGHT</div>
  <div class="footer-brand"><i></i>TLR</div><div class="page-no">4</div><div class="footer-bar"></div>
</section>

<section class="slide s2">
  <div class="header"><h2 class="title">A middle class of 100 million people…</h2><div class="skyline" role="img" aria-label="City skyline silhouette"></div></div>
  <div class="icon-light" role="img" aria-label="Traffic light icon"></div>
  <div class="col-left">
    <h3>POLITICS</h3>
    <p>Brazil launched a fierce battle against poverty 10 years ago with President Ramos. The positive economic environment has helped implement these policies</p>
    <ul>
      <li class="main">Growth Acceleration Program (2007-10): R$400B (*)</li>
      <li class="sub">Public investments in infrastructure</li>
      <li class="sub">Lighten the administrative and legal burden on private initiatives and long-term growth</li>
      <li class="sub">Stimulating Credit &amp; Financing for the real estate sector</li>
      <li class="main">Growth Acceleration Program (2011-14): R$960B (*)</li>
      <li class="sub">Better City &amp; Community: R$80B</li>
      <li class="sub">Water, Light, Transportation: R$135B</li>
      <li class="sub">Energy: R$465B</li>
      <li class="sub">Housing: R$278B - public financing and subsidies through various programs, notably Casa Para Todos (CPT) for low and middle classes and Lar Conjunto</li>
    </ul>
  </div>
  <div class="divider"></div><div class="arrow"></div>
  <p class="lead">Strong political will &amp; positive income generation trends constitute grounds for a significant demand in social housing</p>
  <div class="box">
    <h4>EMERGENCE OF THE MIDDLE CLASS</h4>
    <ul>
      <li>It reached remarkable success: poverty has decreased from 39% of population in 1999 to less than 20% in 2012</li>
      <li>More than 40M people have recently entered the middle class. They need decent housing</li>
      <li class="key">Middle class will represent 54% of the population by the end of 2012 (overall population of 192M)</li>
      <li>Constitution of an upper middle class with an appetite for pricier products</li>
      <li class="key">Housing deficit is estimated to be around 9M, of which 7M in urban housing</li>
    </ul>
  </div>
  <div class="footer-brand"><i></i>TLR</div><div class="page-no">5</div><div class="footer-bar"></div>
</section>

<section class="slide s3">
  <div class="header"><h2 class="title">… and still growing</h2><div class="skyline" role="img" aria-label="City skyline silhouette"></div></div>
  <div class="icon-light" role="img" aria-label="Traffic light icon"></div>
  <p class="sub-lead">Positive demographics &amp; economic environment will sustain the demand</p>

  <svg class="chart" style="left:8px;top:62px" width="150" height="82" viewBox="0 0 150 82">
    <g font-size="4.5">
      <text x="0" y="6">10%</text><text x="2" y="19">8%</text><text x="2" y="32">6%</text><text x="2" y="45">4%</text><text x="2" y="58">2%</text><text x="2" y="71">0%</text>
    </g>
    <line x1="12" y1="70" x2="100" y2="70" stroke="#c9d2dc" stroke-width=".5"/>
    <g fill="#1d4f8c">
      <rect x="15" y="52" width="7" height="18"/><rect x="26" y="56" width="7" height="14"/><rect x="37" y="51" width="7" height="19"/>
      <rect x="48" y="50" width="7" height="20"/><rect x="59" y="54" width="7" height="16"/><rect x="70" y="34" width="7" height="36"/>
      <rect x="81" y="46" width="7" height="24"/><rect x="92" y="50" width="7" height="20"/>
    </g>
    <polyline points="18,9 29,16 40,17 51,20 62,26 73,29 84,33 95,33" fill="none" stroke="#9ec6ea" stroke-width="1.5"/>
    <g font-size="4">
      <text x="104" y="6">■ Real Wages Growth</text><text x="104" y="14" fill="#9ec6ea">■</text><text x="108" y="14">Unemployment Rate</text>
      <text x="14" y="78">2005</text><text x="36" y="78">2007</text><text x="58" y="78">2009</text><text x="80" y="78">2011*</text>
    </g>
  </svg>

  <svg class="chart" style="left:168px;top:60px" width="168" height="85" viewBox="0 0 168 85">
    <g font-size="4.3" text-anchor="end">
      <text x="20" y="6">&gt;70 yrs</text><text x="20" y="15">60-70 yrs</text><text x="20" y="24">50-60 yrs</text><text x="20" y="33">40-50 yrs</text>
      <text x="20" y="42">30-40 yrs</text><text x="20" y="51">20-30 yrs</text><text x="20" y="60">10-20 yrs</text><text x="20" y="69">0-10 yrs</text>
    </g>
    <g fill="#1d4f8c">
      <rect x="22" y="2" width="12" height="3"/><rect x="22" y="11" width="20" height="3"/><rect x="22" y="20" width="34" height="3"/><rect x="22" y="29" width="52" height="3"/>
      <rect x="22" y="38" width="68" height="3"/><rect x="22" y="47" width="90" height="3"/><rect x="22" y="56" width="96" height="3"/><rect x="22" y="65" width="92" height="3"/>
    </g>
    <g fill="#9ec6ea">
      <rect x="22" y="5" width="24" height="3"/><rect x="22" y="14" width="38" height="3"/><rect x="22" y="23" width="58" height="3"/><rect x="22" y="32" width="72" height="3"/>
      <rect x="22" y="41" width="92" height="3"/><rect x="22" y="50" width="96" height="3"/><rect x="22" y="59" width="84" height="3"/><rect x="22" y="68" width="76" height="3"/>
    </g>
    <g font-size="4"><text x="122" y="6">■ 2000 (176M)</text><text x="122" y="13" fill="#9ec6ea">■</text><text x="126" y="13">2020 (208M)</text>
      <text x="20" y="80">0M</text><text x="52" y="80">10M</text><text x="86" y="80">20M</text><text x="118" y="80">30M</text><text x="150" y="80">40M</text></g>
  </svg>

  <div class="buyers">
    <h3>END-BUYERS</h3>
    <ul>
      <li>Aging population: <span class="hi">Average number of persons per household shrunk from 3.7 in 1991 to 3.1 in 2010</span> (1). Expected to remain around 3</li>
      <li>Projection of 12M more people by 2020</li>
      <li class="out">Natural increase in number of households / housing demand</li>
      <li>Low and stable <span class="hi">unemployment rate</span>, 6%</li>
      <li><span class="hi">Considerable growth in real wages</span>, average 5.5% from 2005-2013</li>
      <li class="out">20M more people will have entered Class C from 2008 to 2014</li>
    </ul>
  </div>

  <svg class="chart" style="left:168px;top:150px" width="168" height="80" viewBox="0 0 168 80">
    <text x="40" y="6" font-size="4.3">Number of people per household income (2)</text>
    <g font-size="4.3" text-anchor="end"><text x="12" y="15">200M</text><text x="12" y="30">150M</text><text x="12" y="45">100M</text><text x="12" y="60">50M</text><text x="12" y="75">0M</text></g>
    <g>
      <rect x="22" y="20" width="16" height="10" fill="#dfe9f4"/><rect x="22" y="30" width="16" height="14" fill="#9ec6ea"/><rect x="22" y="44" width="16" height="22" fill="#3d8fd6"/><rect x="22" y="66" width="16" height="8" fill="#1d4f8c"/>
      <rect x="48" y="18" width="16" height="8" fill="#dfe9f4"/><rect x="48" y="26" width="16" height="12" fill="#9ec6ea"/><rect x="48" y="38" width="16" height="26" fill="#3d8fd6"/><rect x="48" y="64" width="16" height="10" fill="#1d4f8c"/>
      <rect x="74" y="16" width="16" height="6" fill="#dfe9f4"/><rect x="74" y="22" width="16" height="10" fill="#9ec6ea"/><rect x="74" y="32" width="16" height="30" fill="#3d8fd6"/><rect x="74" y="62" width="16" height="12" fill="#1d4f8c"/>
    </g>
    <g font-size="4">
      <text x="100" y="20" fill="#dfe9f4">■</text><text x="104" y="20">Class E, &lt;R$800</text>
      <text x="100" y="34" fill="#9ec6ea">■</text><text x="104" y="34">Class D, R$800-1,100</text>
      <text x="100" y="48" fill="#3d8fd6">■</text><text x="104" y="48">Class C, R$1,100-4,800</text>
      <text x="100" y="62" fill="#1d4f8c">■</text><text x="104" y="62">Class A/B, &gt;R$4,800</text>
    </g>
  </svg>

  <div class="footer-brand"><i></i>TLR</div><div class="page-no">6</div><div class="footer-bar"></div>
</section>

</body>
</html>
```